The Brandwell Firm

We need a new design for our letterhead and envelopes. We are a personal injury and criminal defense firm so we need something modern and clean, but more on the professional/traditional side. Our new logo has two colors and is attached to the file so we need something that works well with those colors/matches the design. The following information needs to be on the letterhead:
Phone: (555) 214-3370
Fax: (555) 214-5186
Toll-Free: (888) 431-2059
Post Office Box 4721
Millbrook, SC 29555-4721
HarmClaimCounsel.example
PalmettoTrialAdvocates.example

Target Market(s)

Clients, government agencies, other law firms

Industry/Entity Type

Legal

Font styles to use
Sans Serif
Other font styles liked:
• Arial

Colors

Designer to choose colors to be used in the design.

Requirements
Must have
• Must look professional and clean, modern
Nice to have
• I would like to see a design that works with the logo but does not distract from the content that will be printed on it
Should not have
• Too many colors or crazy designs.

```html
<!DOCTYPE html>
<html lang="en">
<head>
<meta charset="utf-8">
<title>The Brandwell Firm — Letterhead</title>
<link rel="stylesheet" href="https://fonts.googleapis.com/css2?family=Open+Sans:wght@400;600&display=swap">
<style>
  :root {
    --backdrop: #e6e6e8;
    --paper: #ffffff;
    --ink: #454545;
    --navy: #2e3192;
    --red: #d7262e;
    --blush: #fbecee;
  }
  * { margin: 0; padding: 0; box-sizing: border-box; }
  html, body {
    width: 1200px; height: 1200px; overflow: hidden;
    background: var(--backdrop);
    font-family: "Open Sans", Arial, sans-serif;
  }
  .letterhead {
    position: absolute; left: 195px; top: 26px;
    width: 810px; height: 1148px;
    background: var(--paper);
    overflow: hidden;
  }
  .brand {
    position: absolute; left: 52px; top: 108px;
    display: flex; align-items: center; gap: 12px;
  }
  .brand-dot { width: 18px; height: 18px; border-radius: 50%; background: var(--red); }
  .brand-name {
    font-weight: 600; font-size: 28px; color: var(--navy); letter-spacing: 0.5px;
  }
  .contact {
    position: absolute; right: 51px; top: 66px;
    text-align: right; color: var(--ink); font-size: 12.5px; line-height: 16px;
  }
  .contact address { font-style: normal; margin-bottom: 7px; }
  .contact ul { list-style: none; }
  .contact li {
    display: flex; justify-content: flex-end; align-items: center;
    gap: 7px; height: 17.3px;
  }
  .contact svg { width: 12px; height: 12px; fill: none; stroke: var(--navy); stroke-width: 1.6; }
  .accent-bar {
    position: absolute; right: 0; top: 69px; width: 12px; height: 119px; background: var(--red);
  }
  .corner-glow {
    position: absolute; right: 0; bottom: 0; width: 310px; height: 340px;
    background: radial-gradient(ellipse at 85% 85%, var(--blush) 0%, var(--blush) 45%, rgba(251,236,238,0) 75%);
  }
</style>
</head>
<body>
  <main class="letterhead">
    <div class="brand">
      <span class="brand-dot"></span>
      <span class="brand-name">The Brandwell Firm</span>
    </div>

    <div class="contact">
      <address>P.O.&nbsp; Box 4721 Millbrook,<br>SC 29555-4721</address>
      <ul>
        <li>(555) 214-3370
          <svg viewBox="0 0 12 12"><path d="M2 1.5l2 0 1 2.5-1.3 1a6 6 0 0 0 3.3 3.3l1-1.3 2.5 1v2a1 1 0 0 1-1 1A9 9 0 0 1 1 2.5a1 1 0 0 1 1-1z" fill="var(--navy)" stroke="none"/></svg></li>
        <li>(555) 214-5186
          <svg viewBox="0 0 12 12"><rect x="3" y="1.5" width="6" height="3"/><rect x="1.5" y="4.5" width="9" height="4"/><rect x="3" y="7" width="6" height="3.5"/></svg></li>
        <li>(888) 431-2059 (Toll-Free)
          <svg viewBox="0 0 12 12"><path d="M2 1.5l2 0 1 2.5-1.3 1a6 6 0 0 0 3.3 3.3l1-1.3 2.5 1v2a1 1 0 0 1-1 1A9 9 0 0 1 1 2.5a1 1 0 0 1 1-1z" fill="var(--navy)" stroke="none"/></svg></li>
        <li>HarmClaimCounsel.example
          <svg viewBox="0 0 12 12"><circle cx="6" cy="6" r="4.8"/><ellipse cx="6" cy="6" rx="2" ry="4.8"/><path d="M1.2 6h9.6"/></svg></li>
        <li>PalmettoTrialAdvocates.example
          <svg viewBox="0 0 12 12"><circle cx="6" cy="6" r="4.8"/><ellipse cx="6" cy="6" rx="2" ry="4.8"/><path d="M1.2 6h9.6"/></svg></li>
      </ul>
    </div>

    <div class="accent-bar"></div>
    <div class="corner-glow" role="img" aria-label="Faint brand emblem watermark in soft red in the lower right corner"></div>
  </main>
</body>
</html>
```